Roofing web site brvt roofing

Look at some of our competitors web page we like something similar with NYC roofing
https://www.quillbarroofing.example/
Maybe a skyline picture of nyc at the home page with a picture of flat roofing installation

Target Market(s)

Commercial and residential flat roofs

Industry/Entity Type

Flat Roofing industry

Coding

Coded - Design and coding required

Number of Pages Required

2 page

Font styles to use
Decorative
Script

Colors

Designer to choose colors to be used in the design.

Requirements
Must have
• At BRVT Roofing, we are a trusted and reputable roofing company specializing in new construction flat roof installation and repair. With years of experience in the industry, we take pride in providing exceptional roofing solutions to our valued clients. Our team of highly skilled and dedicated roofing professionals understands the unique challenges and requirements of new construction projects. We work closely with builders, contractors, and architects to design and install flat roofs that meet the specific needs of each project. From commercial buildings to residential complexes, we have the expertise to deliver reliable and durable roofing solutions. When it comes to flat roof repairs, we are your go-to experts. Our experienced technicians conduct thorough inspections to identify the root cause of any issues your roof may be experiencing. We utilize the latest industry techniques and high-quality materials to efficiently repair your flat roof, ensuring its integrity and longevity. At BRVT Roofing, we prioritize customer satisfaction above all else. We believe in building strong relationships with our clients by providing exceptional craftsmanship and outstanding customer service. Our team is dedicated to delivering projects on time, within budget, and to the highest standards of quality. We understand that a well-maintained roof is essential for protecting your property and ensuring the safety of its occupants. That's why we use only the best materials and employ skilled professionals who are trained in the latest roofing practices. Our commitment to excellence is evident in every project we undertake. As a fully licensed and insured roofing company, we prioritize safety and adhere to industry regulations and best practices. We take every precaution to create a safe working environment for our team and minimize any disruptions to your daily routine. When you choose BRVT Roofing, you can trust that you are working with a reliable and reputable company that will deliver exceptional results. We are committed to exceeding your expectations and providing you with a roof that is built to last. Contact us today for all your new construction flat roof installation and repair needs.
Nice to have
• NYC skyline background with commercial roofing pictures of torching roofing

```html
<!DOCTYPE html>
<html lang="en">
<head>
<meta charset="utf-8">
<title>BRVT Roofing</title>
<link rel="stylesheet" href="https://fonts.googleapis.com/css2?family=Montserrat:wght@400;500;600;700;800&family=Poppins:wght@300;400;500;600&display=swap">
<style>
:root{
  --orange:#f26a21;
  --black:#0b0b0b;
  --white:#ffffff;
  --ink:#222222;
  --muted:#6d6d6d;
  --light:#f1f1f1;
  --line:#dddddd;
}
*{box-sizing:border-box;margin:0;padding:0}
html,body{width:1200px;height:4100px;overflow:hidden}
body{font-family:"Poppins",sans-serif;color:var(--ink);background:var(--white);position:relative}
h1,h2,h3,.brand,.btn{font-family:"Montserrat",sans-serif}
.abs{position:absolute}

/* header */
.site-header{position:absolute;top:0;left:0;width:1200px;height:80px;background:var(--white);border-top:5px solid var(--orange)}
.brand{position:absolute;left:112px;top:16px;font-weight:700;font-size:21px;line-height:22px;color:var(--black)}
.main-nav{position:absolute;left:392px;top:30px;display:flex;gap:30px;font-family:"Montserrat",sans-serif;font-size:12px;font-weight:600;color:var(--ink)}
.main-nav .active{color:var(--orange);border-bottom:2px solid var(--orange);padding-bottom:4px}
.call-btn{position:absolute;left:920px;top:22px;width:152px;height:36px;background:var(--orange);color:var(--white);font-size:12px;font-weight:600;display:flex;align-items:center;justify-content:center;border-radius:2px}

/* hero */
.hero{position:absolute;top:80px;left:0;width:1200px;height:585px;background:linear-gradient(180deg,#5a6470 0%,#3b434c 45%,#2a2e33 100%)}
.hero-title{position:absolute;top:230px;width:100%;text-align:center;color:var(--white);font-size:46px;font-weight:700}
.hero-arrow{position:absolute;top:262px;width:44px;height:44px;border-radius:50%;background:var(--white);display:flex;align-items:center;justify-content:center}
.services{position:absolute;top:316px;left:380px;width:440px;display:flex;justify-content:space-between}
.service{width:140px;text-align:center;color:var(--white);font-size:14px;font-weight:600}
.service-icon{width:86px;height:86px;border-radius:50%;border:4px solid var(--white);margin:0 auto 10px;background:linear-gradient(135deg,#9aa3ad,#5d6670)}

/* about */
.about{position:absolute;top:665px;left:0;width:1200px;height:680px;background:var(--white)}
.about-frame{position:absolute;left:120px;top:230px;width:200px;height:300px;border:14px solid var(--orange);border-right:none}
.about-photo-a{position:absolute;left:196px;top:110px;width:324px;height:260px;background:linear-gradient(135deg,#6f7d8b,#c7ccd1)}
.about-photo-b{position:absolute;left:320px;top:270px;width:250px;height:280px;background:linear-gradient(180deg,#6fa3d8,#d9e6f2)}
.eyebrow{font-size:13px;letter-spacing:4px;color:var(--orange);font-weight:500}
.about-copy{position:absolute;left:600px;top:105px;width:410px}
.about-copy h2{font-size:40px;font-weight:800;color:var(--black);margin:8px 0 18px}
.about-copy p{font-size:12.5px;line-height:23px;color:var(--muted);text-align:justify}
.btn{display:inline-block;background:var(--orange);color:var(--white);font-size:12px;font-weight:700;padding:12px 26px;margin-top:22px;border-radius:2px}
.side-word{position:absolute;left:1080px;top:40px;writing-mode:vertical-rl;font-family:"Montserrat",sans-serif;font-size:84px;font-weight:800;color:#f3f3f3;letter-spacing:10px}

/* why */
.why{position:absolute;top:1345px;left:0;width:1200px;height:560px;background:var(--black)}
.why h2{position:absolute;left:112px;top:100px;color:var(--white);font-size:44px;font-weight:800}
.why-list{position:absolute;left:112px;top:180px;list-style:none;color:var(--white);font-size:16px}
.why-list li{display:flex;align-items:center;gap:16px;height:38px}
.why-frame{position:absolute;left:720px;top:80px;width:260px;height:120px;border:16px solid var(--orange);border-bottom:none}
.why-photo{position:absolute;left:600px;top:112px;width:400px;height:330px;background:linear-gradient(160deg,#c8613b,#8d3d22)}

/* portfolio */
.portfolio{position:absolute;top:1905px;left:0;width:1200px;height:815px;background:var(--orange)}
.portfolio .eyebrow{position:absolute;top:88px;width:100%;text-align:center;color:var(--white)}
.portfolio h2{position:absolute;top:110px;width:100%;text-align:center;color:var(--white);font-size:46px;font-weight:700}
.tile{position:absolute}

/* testimonials */
.testimonials{position:absolute;top:2720px;left:0;width:1200px;height:540px;background:var(--white);text-align:center;overflow:hidden}
.testimonials h2{margin-top:80px;font-size:44px;font-weight:600;color:var(--black)}
.stars{color:var(--orange);font-size:16px;letter-spacing:3px;margin-top:8px}
.quote{width:600px;margin:10px auto 0;font-size:15px;line-height:26px;color:var(--muted)}
.name{font-weight:600;font-size:16px;color:var(--black);margin-top:20px}
.role{font-size:12px;color:var(--muted)}
.quote-faded{position:absolute;top:202px;width:180px;font-size:13px;line-height:24px;color:#c9c9c9;text-align:left}
.slider{position:absolute;left:350px;top:378px;width:500px;height:4px;background:var(--line)}
.slider span{display:block;width:170px;height:4px;background:var(--orange);margin-left:0}

/* contact */
.contact{position:absolute;top:3260px;left:0;width:1200px;height:440px;background:linear-gradient(180deg,var(--white) 0%,var(--white) 20%,#ececec 20%)}
.contact-card{position:absolute;left:200px;top:-60px;width:800px;height:460px;background:var(--white);border-bottom:8px solid var(--orange);box-shadow:0 6px 24px rgba(0,0,0,.12)}
.contact-card h2{text-align:center;margin-top:44px;font-size:38px;font-weight:600;color:var(--black)}
.field{position:absolute;height:54px;border:1px solid var(--line);font-size:13px;color:#9a9a9a;padding:16px 20px}
.submit{position:absolute;left:325px;top:388px;width:150px;height:40px;background:var(--orange);color:var(--white);font-family:"Montserrat",sans-serif;font-size:12px;font-weight:700;display:flex;align-items:center;justify-content:center}

/* footer */
.site-footer{position:absolute;top:3700px;left:0;width:1200px;height:400px;background:var(--black);color:var(--white)}
.site-footer .brand{color:var(--white);top:62px}
.footer-about{position:absolute;left:112px;top:125px;width:220px;font-size:13px;line-height:24px;color:#cfcfcf}
.footer-col{position:absolute;top:62px}
.footer-col h3{font-size:20px;font-weight:700;margin-bottom:18px}
.footer-col ul{list-style:none;font-size:13px;line-height:27px;color:#d6d6d6}
.footer-col li{display:flex;gap:10px;align-items:flex-start}
.dot{display:inline-block;width:8px;height:8px;border-radius:50%;background:var(--orange);margin-top:10px;flex:none}
.copyright{position:absolute;bottom:0;left:0;width:1200px;height:58px;border-top:1px solid #2a2a2a;display:flex;align-items:center;justify-content:center;font-size:12px;color:#cfcfcf;gap:8px}
</style>
</head>
<body>

<header class="site-header">
  <div class="brand">BRVT<br>Roofing</div>
  <nav class="main-nav">
    <span class="active">HOME</span><span>ABOUT</span><span>SERVICES</span><span>GALLERY</span><span>TESTIMONIALS</span><span>CONTACT</span>
  </nav>
  <div class="call-btn">&#9742;&nbsp; 555-014-2290</div>
</header>

<section class="hero" role="img" aria-label="City skyline behind a roofer working on a flat roof installation">
  <div class="hero-arrow" style="left:34px"><svg width="14" height="14" viewBox="0 0 14 14"><path d="M9 2 L4 7 L9 12" stroke="#222" stroke-width="2" fill="none"/></svg></div>
  <div class="hero-arrow" style="right:34px"><svg width="14" height="14" viewBox="0 0 14 14"><path d="M5 2 L10 7 L5 12" stroke="#222" stroke-width="2" fill="none"/></svg></div>
  <h1 class="hero-title">BRVT Roofing</h1>
  <div class="services">
    <div class="service"><div class="service-icon" role="img" aria-label="Roof leak repair photo"></div>Roof Leak Repairs</div>
    <div class="service"><div class="service-icon" role="img" aria-label="Flashing services photo"></div>Flashing Services</div>
    <div class="service"><div class="service-icon" role="img" aria-label="Waterproofing photo"></div>Waterproofing Experts</div>
  </div>
</section>

<section class="about">
  <div class="about-frame"></div>
  <div class="about-photo-a" role="img" aria-label="Roofer installing flat roof membrane"></div>
  <div class="about-photo-b" role="img" aria-label="Skylight on a flat roof under blue sky"></div>
  <div class="about-copy">
    <div class="eyebrow">ABOUT US</div>
    <h2>BRVT ROOFING</h2>
    <p>At BRVT Roofing, we are a trusted and reputable roofing company specializing in new construction flat roof installation and repair. With years of experience in the industry, we take pride in providing exceptional roofing solutions to our valued clients. Our team of highly skilled and dedicated roofing professionals understands the unique challenges and requirements of new construction projects. We work closely with builders, contractors, and architects to design and install flat roofs that meet the specific needs of each project. From commercial buildings to residential complexes, we have the expertise to deliver reliable and durable roofing solutions. When it comes to flat roof repairs, we are your go-to experts. Our experienced technicians conduct thorough inspections to identify the root cause of any issues your roof may be experiencing.</p>
    <span class="btn">MEET THE TEAM</span>
  </div>
  <div class="side-word">ABOUT US</div>
</section>

<section class="why">
  <h2>WHY CHOOSE US</h2>
  <ul class="why-list">
    <li><svg width="22" height="22" viewBox="0 0 22 22"><circle cx="11" cy="11" r="10" fill="none" stroke="#f26a21" stroke-width="2"/><path d="M6 11 L10 15 L16 7" stroke="#f26a21" stroke-width="2.4" fill="none"/></svg>Licensed, Bonded, &amp; Insured</li>
    <li><svg width="22" height="22" viewBox="0 0 22 22"><circle cx="11" cy="11" r="10" fill="none" stroke="#f26a21" stroke-width="2"/><path d="M6 11 L10 15 L16 7" stroke="#f26a21" stroke-width="2.4" fill="none"/></svg>Reliable &amp; Experienced Professionals</li>
    <li><svg width="22" height="22" viewBox="0 0 22 22"><circle cx="11" cy="11" r="10" fill="none" stroke="#f26a21" stroke-width="2"/><path d="M6 11 L10 15 L16 7" stroke="#f26a21" stroke-width="2.4" fill="none"/></svg>Free Evaluations &amp; Estimates</li>
    <li><svg width="22" height="22" viewBox="0 0 22 22"><circle cx="11" cy="11" r="10" fill="none" stroke="#f26a21" stroke-width="2"/><path d="M6 11 L10 15 L16 7" stroke="#f26a21" stroke-width="2.4" fill="none"/></svg>Lead-Safe Certified</li>
    <li><svg width="22" height="22" viewBox="0 0 22 22"><circle cx="11" cy="11" r="10" fill="none" stroke="#f26a21" stroke-width="2"/><path d="M6 11 L10 15 L16 7" stroke="#f26a21" stroke-width="2.4" fill="none"/></svg>24/7 Emergency Response</li>
    <li><svg width="22" height="22" viewBox="0 0 22 22"><circle cx="11" cy="11" r="10" fill="none" stroke="#f26a21" stroke-width="2"/><path d="M6 11 L10 15 L16 7" stroke="#f26a21" stroke-width="2.4" fill="none"/></svg>Top-Rated Local Business</li>
  </ul>
  <div class="why-frame"></div>
  <div class="why-photo" role="img" aria-label="Roofer working on a tiled roof with skylights"></div>
</section>

<section class="portfolio">
  <div class="eyebrow">GALLERY</div>
  <h2>OUR PORTFOLIO</h2>
  <div class="tile" style="left:110px;top:195px;width:490px;height:610px;background:linear-gradient(180deg,#4d6a52 0%,#7f8a86 55%,#3a3a3a 100%)" role="img" aria-label="Roofer rolling out flat roofing membrane"></div>
  <div class="abs" style="left:300px;top:480px;width:60px;height:60px;border-radius:50%;background:#fff;display:flex;align-items:center;justify-content:center;font-size:26px;color:#222">+</div>
  <div class="tile" style="left:600px;top:195px;width:245px;height:305px;background:linear-gradient(180deg,#6fa5de,#ffffff)" role="img" aria-label="House eave against blue sky"></div>
  <div class="tile" style="left:845px;top:195px;width:245px;height:305px;background:linear-gradient(135deg,#c8653a,#8f3f22)" role="img" aria-label="Clay roof tiles"></div>
  <div class="tile" style="left:600px;top:500px;width:245px;height:305px;background:linear-gradient(180deg,#d9d9d9,#9a9a9a)" role="img" aria-label="Gutter and roof edge"></div>
  <div class="tile" style="left:845px;top:500px;width:245px;height:305px;background:linear-gradient(135deg,#d28a5f,#a4532c)" role="img" aria-label="Hands laying roof tiles"></div>
</section>

<section class="testimonials">
  <h2>TESTIMONIALS</h2>
  <div class="stars">&#9733;&#9733;&#9733;&#9733;&#9733;</div>
  <p class="quote">Lorem ipsum dolor sit amet, consectetur adipiscing elit, sed do eiusmod tempor incididunt ut labore et dolore magna aliqua. Ut enim ad minim veniam, quis nostrud exercitation ullamco laboris nisi ut aliquip ex ea commodo consequat.</p>
  <div class="name">John Doe</div>
  <div class="role">Company name</div>
  <div class="quote-faded" style="left:0">Great crew, fast work and a clean site. Our flat roof has stayed dry since they finished.</div>
  <div class="quote-faded" style="right:0;text-align:right">Honest estimate, on time and on budget. We will call them again for the next building.</div>
  <div class="slider"><span></span></div>
</section>

<section class="contact">
  <div class="contact-card">
    <h2>GET IN TOUCH</h2>
    <div class="field" style="left:70px;top:122px;width:320px">Name*</div>
    <div class="field" style="left:410px;top:122px;width:320px">Email Address*</div>
    <div class="field" style="left:70px;top:196px;width:320px">Phone*</div>
    <div class="field" style="left:410px;top:196px;width:320px">Subject*</div>
    <div class="field" style="left:70px;top:270px;width:660px;height:96px">Message*</div>
    <div class="submit">SUBMIT NOW</div>
  </div>
</section>

<footer class="site-footer">
  <div class="brand">BRVT<br>Roofing</div>
  <p class="footer-about">We stay in constant communication with our customers until the job is done. To get a free quote, or if you have questions or special requests, just drop us a line.</p>
  <div class="footer-col" style="left:440px">
    <h3>Information</h3>
    <ul><li><span class="dot"></span>Home</li><li><span class="dot"></span>About us</li><li><span class="dot"></span>Services</li><li><span class="dot"></span>Blog</li><li><span class="dot"></span>Reviews</li><li><span class="dot"></span>Contact us</li></ul>
  </div>
  <div class="footer-col" style="left:668px">
    <h3>Contact</h3>
    <ul>
      <li><span class="dot"></span>Phone :<br>555-014-2290</li>
      <li><span class="dot"></span>Email :<br>hello@brvtroofing.example</li>
      <li><span class="dot"></span>Hours<br>Monday - Friday: 8am - 5pm<br>Saturday - Sunday: 9am-13</li>
    </ul>
  </div>
  <div class="footer-col" style="left:965px">
    <h3>Follow us</h3>
    <ul><li><span class="dot"></span>Newsfeed</li><li><span class="dot"></span>Video Channel</li><li><span class="dot"></span>Photo Feed</li></ul>
  </div>
  <div class="copyright"><span class="dot" style="margin-top:0"></span>Copyright 2024 Company name | All rights reserved</div>
</footer>

</body>
</html>
```